Bifold brochure design for leadership academy

Please see below. This is a bifold brochure for a leadership academy. (www.brv.institute). Look and feel must be colours, shapes, abstract designs, graphics, pictures. Make this professional, yet casual and bold.

Feel free to design just the front and back cover, then I'll give feedback on whether or not you're in the right direction.

COVER
- Title: “The Boldest Bridge Year Journey”
- “Northward Mentor Institute” logo somewhere
- Subtitles (with images, icons, and/or shapes): “Self-discovery” “Skills development” “Real-world Impact”

PAGE 2 (Inside Fold)
- Title: "The Program"
- Section 2a: Section title: "How it works”
- Image: See website, image under "four phases of the program". Please adapt and make it look better
- Text: NMI is a structured, 8-month ‘gap year’ program for 18-25 year olds who want more than just a year off – they want a year ahead. Our aim is to develop high-potential young leaders with strong values, clear purpose, high-impact skills, and a track record of real-world accomplishments that are second-to-none. We do this through four-phases.
- Section 2b: Section title: “Dates & Timing”
- Image: See image on website under 'dates and timing'. Make sure both dates show up on the brochure (September and January program).
- Text: There are two programs per year: one that starts in September, the other in January. The first four months of the program are based in Toronto at the NMI headquarters. The curriculum we work through is highly engaging and personalized, focusing directly on students’ goals. After that, students are out in the world, achieving the remaining components of the program (e.g. internship, volunteer abroad).

PAGE 3 (Outside Fold)
- Page Title: "The Students"
- Section 3a: Section title: “Who’s it for”
- Subtitle1: “High school graduates”
 Image/icon of a high school grad
 Text1: 90% of high school grads aren't sure why they’re going to university or what they want to study.
 Text2: NMI helps students discover what they truly want to do in life, and make enormous progress towards these goals.

- Subtitle2: “Post-secondary students”
 Image/icon of a university / college student
 Text1: 28% of students switch or drop out of their program because it wasn’t for them or they didn’t like it.
 Text2: Don't keep moving around or risk switching careers down the road – find out what sparks your passion with NMI.

- Subtitle3: “Post-secondary graduates”
 Image/icon of a university/ college grad
 Text1: 50% of graduates are unemployed or underemployed, 60% are in debt.
 Text2: NMI will help you get your dream job – our students won’t settle for anything less.

- Section 3b: Section title: “How to apply”
 Text1: We select high-potential young leaders with a desire to improve themselves and impact the world.
 Text2: We won’t ask you for your grades – we care more about your values and potential.
 Text3: Visit www.brv.institute to apply now

BACK COVER
- Page Title: “Get in Touch”
- Website: www.brv.institute
- Facebook page: facebook.com/brv.institute
- Twitter handle: @brv_institute
- Email: tomas@brv.institute

Project Deadline Extended Reason: Made a mistake initially only giving designers 2 days to submit. This allows for more high quality designs. Thank you. Added Wednesday, March 18, 2015

Target Market(s)

18-25 year olds, parents, teachers

Industry/Entity Type

Leadership

Requirements
Must have
• Beautiful design - sleek and bold, yet colourful and casual. Keep the colours similar to our website (www.brv.institute). See examples of other brochures.
• http://img.pelvoro.net/jpg/00/11/22/33/240_F_11223344_xQr8LmPzTw3KdNvBsYcHuJeFa2gkTqWn.jpg
• http://vantoliq.com/wp-content/uploads/2014/11/Real-Estate-Bi-fold-Brochure.jpg
• http://www.murablo.com/media/k2/galleries/5/001-bi-fold-brochure-psd-mock-up-template.jpg
• http://img.pelvoro.net/jpg/00/44/55/66/240_F_44556677_Zk3wPqLm8RtYvBnXcDs2HjKuE5fa9Gq0.jpg

```html
<!DOCTYPE html>
<html lang="en">
<head>
<meta charset="utf-8">
<title>Northward Mentor Institute – The Program</title>
<link rel="stylesheet" href="https://fonts.googleapis.com/css2?family=Montserrat:wght@600;700;800&family=Raleway:wght@400;500;600&display=swap">
<style>
  :root{
    --bg:#e9e9e9;
    --cream:#efe3ad;
    --paper:#f8f4e6;
    --yellow:#f0df3f;
    --gold:#e4c24a;
    --red:#b3212f;
    --blue:#3a72a6;
    --green:#b4c96a;
    --ink:#3b3326;
    --white:#ffffff;
  }
  *{box-sizing:border-box;margin:0;padding:0}
  html,body{width:1200px;height:800px;overflow:hidden;background:var(--bg)}
  body{font-family:"Raleway",sans-serif;color:var(--ink)}
  .spread{position:absolute;left:40px;top:40px;width:1120px;height:720px;display:flex;box-shadow:0 6px 22px rgba(0,0,0,.18)}
  .page{position:relative;width:560px;height:720px;overflow:hidden}
  .page--program{background:var(--cream)}
  .page--students{background:var(--paper)}
  .photo{position:absolute;background:linear-gradient(135deg,#8d6a52,#c99a7c 40%,#7d8aa0)}
  .photo--hero{left:0;top:0;width:560px;height:400px;
    background:linear-gradient(90deg,#7e6553 0%,#c59b7e 35%,#a98a76 55%,rgba(239,227,173,0) 82%),linear-gradient(180deg,#5c4a3d,#b58d71 60%,var(--cream) 100%)}
  .ribbon{position:absolute;background:var(--blue);color:var(--white);font-family:"Montserrat",sans-serif;font-weight:800;text-transform:uppercase;letter-spacing:.5px;display:flex;align-items:center;justify-content:center}
  .ribbon--program{left:320px;top:120px;width:240px;height:56px;font-size:22px}
  .ribbon--students{left:0;top:360px;width:170px;height:44px;font-size:17px}
  .section-title{font-family:"Montserrat",sans-serif;font-weight:800;text-transform:uppercase;font-size:15px;letter-spacing:.3px}
  .how{position:absolute;left:318px;top:190px;width:228px}
  .how .section-title{text-align:center;margin-bottom:8px}
  .body{font-size:11.5px;line-height:1.4}
  .phases{position:absolute;inset:0}
  .phase{position:absolute;width:136px;bottom:0;padding:0 10px}
  .phase:nth-child(odd){background:var(--yellow)}
  .phase:nth-child(even){background:var(--gold)}
  .phase--discover{left:18px;top:410px}
  .phase--design{left:150px;top:430px}
  .phase--build{left:282px;top:450px}
  .phase--achieve{left:414px;top:470px}
  .phase__tag{display:inline-block;background:var(--red);color:var(--white);font-family:"Montserrat",sans-serif;font-weight:700;font-size:13px;padding:5px 14px 5px 8px;margin:12px 0 10px -10px;clip-path:polygon(0 0,100% 0,88% 50%,100% 100%,0 100%)}
  .phase__icon{position:absolute;top:10px;right:8px;width:28px;height:28px}
  .phase .body{font-size:10.5px;line-height:1.35}
  .phase ol{font-size:10.5px;line-height:1.35;padding-left:14px;margin-top:4px}
  .dates{position:absolute;left:30px;top:40px;width:265px}
  .dates .section-title{margin-bottom:8px}
  .timeline{position:absolute;left:300px;top:60px;width:240px;height:250px}
  .photo--group{left:0;top:60px;width:70px;height:140px}
  .month{position:absolute;top:0;width:56px;height:250px;padding:6px 4px}
  .month:nth-of-type(odd){background:var(--yellow)}
  .month:nth-of-type(even){background:var(--gold)}
  .month--aug{left:72px}.month--sep{left:128px}.month--oct{left:184px}
  .month__label{font-family:"Montserrat",sans-serif;font-weight:700;font-size:10px;color:var(--blue);text-align:center;margin-bottom:6px}
  .month__item{font-size:8px;line-height:1.25;margin-bottom:6px}
  .month__item b{color:var(--red)}
  .students{position:absolute;left:0;top:340px;width:560px;height:380px;background:var(--green)}
  .photo--class{left:180px;top:30px;width:160px;height:70px}
  .photo--grads{left:360px;top:30px;width:180px;height:70px}
  .who{position:absolute;left:300px;top:128px;width:240px;text-align:center}
  .audience{position:absolute}
  .audience--hs{left:24px;top:125px;width:250px}
  .audience--post{left:300px;top:245px;width:240px}
  .audience__title{font-family:"Montserrat",sans-serif;font-weight:800;font-size:13px;color:var(--red);text-transform:uppercase;margin-bottom:8px}
  .stat{display:flex;gap:8px;align-items:flex-start;margin-bottom:8px}
  .stat__num{flex:none;background:var(--red);color:var(--white);font-family:"Montserrat",sans-serif;font-weight:700;font-size:24px;width:70px;height:54px;display:flex;align-items:center;justify-content:center;border:2px solid var(--white)}
  .stat .body{font-size:11px}
  .note{font-size:11px;line-height:1.4;font-style:italic}
</style>
</head>
<body>
<main class="spread">
  <section class="page page--program">
    <div class="photo photo--hero" role="img" aria-label="Photo of five smiling young students in front of library bookshelves"></div>
    <h2 class="ribbon ribbon--program">The Program</h2>
    <article class="how">
      <h3 class="section-title">How it works</h3>
      <p class="body">NMI is a structured, 8-month ‘gap year’ program for 18-25 year olds who want more than just a year off – they want a year ahead. Our aim is to develop high-potential young leaders with strong values, clear purpose, high-impact skills, and a track record of real-world accomplishments that are second-to-none. We do this through four-phases.</p>
    </article>
    <div class="phases">
      <div class="phase phase--discover">
        <span class="phase__tag">Discover</span>
        <svg class="phase__icon" viewBox="0 0 34 34" aria-hidden="true"><circle cx="17" cy="17" r="15" fill="none" stroke="#111" stroke-width="2"/><circle cx="17" cy="17" r="9" fill="#111"/><polygon points="17,9 19,17 17,25 15,17" fill="#f0df3f"/></svg>
        <p class="body">Discover your strengths, development areas, personality style, passions and other attributes through a highly personalized transformation program.</p>
      </div>
      <div class="phase phase--design">
        <span class="phase__tag">Design</span>
        <svg class="phase__icon" viewBox="0 0 34 34" aria-hidden="true"><path d="M8 3h14l5 5v23H8z" fill="#fff" stroke="#111" stroke-width="2"/><path d="M12 12h11M12 17h11M12 22h7" stroke="#111" stroke-width="2"/></svg>
        <p class="body">Design your year in the program and learn how to manage goals through our advanced goal-setting training.</p>
      </div>
      <div class="phase phase--build">
        <span class="phase__tag">Build</span>
        <svg class="phase__icon" viewBox="0 0 34 34" aria-hidden="true"><rect x="2" y="20" width="10" height="12" fill="#111"/><rect x="12" y="12" width="10" height="20" fill="#111"/><rect x="22" y="24" width="10" height="8" fill="#111"/><circle cx="17" cy="6" r="4" fill="#111"/></svg>
        <p class="body">Build a set of skills that will directly help you achieve your goals, including issue-based problem solving, creativity, and structured communications.</p>
      </div>
      <div class="phase phase--achieve">
        <span class="phase__tag">Achieve</span>
        <svg class="phase__icon" viewBox="0 0 34 34" aria-hidden="true"><path d="M9 3h16v8a8 8 0 0 1-16 0z" fill="#111"/><rect x="15" y="19" width="4" height="7" fill="#111"/><rect x="10" y="26" width="14" height="5" fill="#111"/></svg>
        <p class="body">Achieve six things before you can graduate:</p>
        <ol>
          <li>Solve a social problem</li>
          <li>Conquer a physical feat</li>
          <li>Organize an event</li>
          <li>Volunteer abroad</li>
          <li>Start something</li>
          <li>Do an internship</li>
        </ol>
      </div>
    </div>
  </section>

  <section class="page page--students">
    <article class="dates">
      <h3 class="section-title">Dates &amp; Timing</h3>
      <p class="body">There are two programs per year: one that starts in September, the other in January. The first four months of the program are based in Toronto at the NMI headquarters. The curriculum we work through is highly engaging and personalized, focusing directly on students’ goals. After that, students are out in the world, achieving the remaining components of the program (e.g. internship, volunteer abroad).</p>
    </article>
    <div class="timeline">
      <div class="photo photo--group" role="img" aria-label="Photo of a small group of young students"></div>
      <div class="month month--aug">
        <p class="month__label">AUG</p>
        <p class="month__item"><b>Discover:</b> find your passion &amp; direction</p>
        <p class="month__item"><b>Design:</b> design your goals</p>
      </div>
      <div class="month month--sep">
        <p class="month__label">SEP</p>
        <p class="month__item"><b>Build:</b> build relevant skills</p>
        <p class="month__item"><b>Achieve:</b> crush your goals</p>
      </div>
      <div class="month month--oct">
        <p class="month__label">OCT</p>
        <p class="month__item"><b>Conquer</b> a physical feat</p>
        <p class="month__item"><b>Organize</b> an event</p>
      </div>
    </div>

    <div class="students">
      <div class="photo photo--class" role="img" aria-label="Photo of students in a classroom"></div>
      <div class="photo photo--grads" role="img" aria-label="Photo of a group of smiling graduates"></div>
      <h3 class="section-title who">Who’s it for</h3>
      <div class="audience audience--hs">
        <h4 class="audience__title">High school graduates</h4>
        <div class="stat"><span class="stat__num">90%</span><p class="body">of high school grads aren't sure why they’re going to university or what they want to study.</p></div>
        <p class="note">NMI helps students discover what they truly want to do in life, and make enormous progress towards these goals.</p>
      </div>
      <div class="audience audience--post">
        <h4 class="audience__title">Post-secondary students</h4>
        <div class="stat"><span class="stat__num">28%</span><p class="body">of students switch or drop out of their program because it wasn’t for them.</p></div>
        <p class="note">Don't keep moving around – find out what sparks your passion with NMI.</p>
      </div>
    </div>
    <h2 class="ribbon ribbon--students">The Students</h2>
  </section>
</main>
</body>
</html>
```